KRV Business Card

Looking for a business card for my restaurant group I own. Four different concepts:

Copperfield Alehouse
Bristow Alehouse
Tanager's Stone Hearth Kitchen
Pellston Patty Company

Card doesn't need to include all the logos.

```html
<!DOCTYPE html>
<html lang="en">
<head>
<meta charset="utf-8">
<title>KRV Business Card</title>
<link href="https://fonts.googleapis.com/css2?family=Poppins:wght@400;500;600&display=swap" rel="stylesheet">
<style>
  :root {
    --backdrop: #1f1d1d;
    --paper: #ffffff;
    --gold: #d1ae6b;
    --slate: #6f6f71;
    --ink: #4a4a4c;
    --rule: #8a8a8a;
  }
  * { margin: 0; padding: 0; box-sizing: border-box; }
  html, body {
    width: 1125px;
    height: 1200px;
    overflow: hidden;
    background: var(--backdrop);
    font-family: "Poppins", sans-serif;
  }
  .card {
    position: absolute;
    left: 171px;
    width: 826px;
    height: 472px;
  }
  .card-front { top: 106px; background: var(--paper); }
  .card-back { top: 639px; background: var(--gold); }

  .accent-bar {
    position: absolute;
    left: 0; top: 55px;
    width: 12px; height: 61px;
    background: var(--slate);
  }
  .holder-name {
    position: absolute;
    left: 46px; top: 50px;
    font-size: 31px;
    font-weight: 600;
    color: var(--gold);
    line-height: 1.2;
  }
  .holder-title {
    position: absolute;
    left: 46px; top: 88px;
    font-size: 21px;
    color: var(--slate);
    line-height: 1.2;
  }
  .divider {
    position: absolute;
    left: 47px; top: 165px;
    width: 130px; height: 1px;
    background: var(--rule);
  }
  .contact {
    position: absolute;
    left: 46px; top: 225px;
    font-size: 20px;
    color: var(--ink);
    line-height: 25.5px;
  }
  .contact .address { margin-bottom: 9px; }

  .brand-name {
    position: absolute;
    right: 58px; top: 258px;
    width: 300px;
    text-align: center;
    font-size: 40px;
    font-weight: 600;
    color: var(--gold);
    line-height: 1.15;
    letter-spacing: 3px;
    text-transform: uppercase;
  }

  .back-initials {
    position: absolute;
    left: 0; right: 0; top: 108px;
    text-align: center;
    font-size: 190px;
    font-weight: 600;
    color: var(--paper);
    line-height: 1;
    letter-spacing: 6px;
  }
  .back-url {
    position: absolute;
    left: 0; right: 0; top: 391px;
    text-align: center;
    font-size: 19px;
    color: var(--paper);
    letter-spacing: 4.2px;
    text-transform: uppercase;
  }
</style>
</head>
<body>
  <section class="card card-front">
    <div class="accent-bar"></div>
    <h1 class="holder-name">Daniel Hartley</h1>
    <p class="holder-title">President</p>
    <div class="divider"></div>
    <div class="contact">
      <p class="address">4120 Alder Court<br>Juneau, Alaska 34781</p>
      <p>(P) 555-214-7730<br>(M) 555-318-6042<br>(F) 555-427-1895<br>name@kestrelridgeventures.com<br>www.kestrelridgeventures.com</p>
    </div>
    <p class="brand-name">Kestrel Ridge Ventures</p>
  </section>

  <section class="card card-back">
    <p class="back-initials">KRV</p>
    <p class="back-url">www.kestrelridgeventures.com</p>
  </section>
</body>
</html>
```